Business card for a Exhibition booth fabrication company

Hi. My company would like to change our corporate name card. We are an events and Exhibition stand builder company. We would like our corporate name card to resonate what we do. I need someone to create something unique that relates to the industry that I am in. The graphic designer should be creative to incorporate the elements of my industry and try to blend in well in the design of the card. Our aim is to ensure that we are unique and our card can look different from our competitors.
Updates

Target Market(s)

Marketing and events manager from all companies

Contact Information for Business Card

The business card should have the following details:
Name
Job Title
Email
Website

Colors

Designer to choose colors to be used in the design.

Requirements
Must have
• The card must be look something that is relevant to the service that I am providing. My website is: www.velmora-buildworks.com
• You can see my website to get more information on what service that I am doing
Nice to have
• On the back of my card, I would like to have a globe image with the incorporation of my company logo. This is to indicate that my services can be done in any part of the world.

```html
<!DOCTYPE html>
<html lang="en">
<head>
<meta charset="utf-8">
<title>Velmora Buildworks — Business Card</title>
<link rel="stylesheet" href="https://fonts.googleapis.com/css2?family=Catamaran:wght@400;500;600;700&display=swap">
<style>
  :root {
    --backdrop: #3a3a3c;
    --card-white: #ffffff;
    --card-grey-light: #e6e6e6;
    --card-grey-dark: #bdbdbd;
    --brand-red: #e3141b;
    --ink: #111111;
    --ink-grey: #555555;
    --map-light: #f4f4f4;
    --map-mid: #d2d2d2;
  }
  * { box-sizing: border-box; margin: 0; padding: 0; }
  html, body {
    width: 1200px; height: 1000px; overflow: hidden;
    background: var(--backdrop);
    font-family: "Catamaran", sans-serif;
  }
  .canvas {
    width: 1200px; height: 1000px;
    display: flex; flex-direction: column; align-items: center; justify-content: center;
    gap: 40px;
  }
  .card {
    width: 735px; height: 420px; border-radius: 28px;
    position: relative; overflow: hidden;
  }

  /* Back side */
  .card-back {
    background: radial-gradient(ellipse at 55% 45%, var(--card-grey-light), var(--card-grey-dark));
  }
  .network-map {
    position: absolute; left: 60px; top: 30px; width: 615px; height: 360px;
    border-radius: 40% 45% 40% 50%;
    background: radial-gradient(ellipse at 50% 45%, var(--map-light) 0%, var(--map-mid) 70%, transparent 100%);
    opacity: 0.85;
  }
  .brand-back {
    position: absolute; inset: 0;
    display: flex; align-items: center; justify-content: center; gap: 14px;
  }
  .brand-dot {
    width: 26px; height: 26px; border-radius: 50%; background: var(--brand-red);
  }
  .brand-name {
    font-weight: 600; letter-spacing: 3px; color: var(--ink-grey);
    text-transform: uppercase;
  }
  .brand-back .brand-name { font-size: 30px; }

  /* Front side */
  .card-front { background: var(--card-white); }
  .brand-front {
    position: absolute; left: 40px; top: 150px; width: 320px;
    display: flex; align-items: center; gap: 12px;
  }
  .brand-front .brand-name { font-size: 22px; letter-spacing: 2px; }
  .divider {
    position: absolute; left: 375px; top: 50px; width: 2px; height: 215px;
    background: var(--brand-red);
  }
  .contact {
    position: absolute; left: 400px; top: 48px; color: var(--ink);
  }
  .contact-name { font-size: 27px; font-weight: 600; color: var(--brand-red); line-height: 1.05; }
  .contact-title { font-size: 17px; font-weight: 500; margin-bottom: 8px; }
  .contact-label { font-size: 16px; font-weight: 500; color: var(--brand-red); line-height: 1.1; margin-top: 4px; }
  .contact-value { font-size: 20px; font-weight: 500; line-height: 1.15; }
  .contact-row { display: flex; align-items: center; gap: 8px; font-size: 19px; font-weight: 500; margin-top: 4px; }
  .contact-row svg { width: 18px; height: 18px; flex: none; }
  .accent { color: var(--brand-red); }

  .services {
    position: absolute; left: 30px; right: 30px; top: 290px; text-align: center;
  }
  .services-heading { font-size: 18px; font-weight: 500; color: var(--brand-red); letter-spacing: 0.5px; }
  .services-list { font-size: 15px; font-weight: 500; color: var(--ink); line-height: 1.3; margin-top: 2px; }
</style>
</head>
<body>
<main class="canvas">
  <section class="card card-back" aria-label="Card back">
    <div class="network-map" role="img" aria-label="World map with glowing connection lines linking cities across continents"></div>
    <div class="brand-back">
      <span class="brand-dot"></span>
      <span class="brand-name">Velmora Buildworks</span>
    </div>
  </section>

  <section class="card card-front" aria-label="Card front">
    <div class="brand-front">
      <span class="brand-dot"></span>
      <span class="brand-name">Velmora Buildworks</span>
    </div>

    <div class="divider"></div>

    <div class="contact">
      <p class="contact-name">Adrian Kell</p>
      <p class="contact-title">President</p>
      <p class="contact-label">Singapore Contact:</p>
      <p class="contact-value">+65 81402297</p>
      <p class="contact-label">Qatar Contact:</p>
      <p class="contact-value">+974 55284410</p>
      <p class="contact-row">
        <svg viewBox="0 0 20 20"><rect x="1" y="4" width="18" height="12" rx="2" fill="var(--brand-red)"/><path d="M2 5 L10 11 L18 5" stroke="#fff" stroke-width="1.6" fill="none"/></svg>
        info@velmora-buildworks.com
      </p>
      <p class="contact-row">
        <svg viewBox="0 0 20 20"><circle cx="10" cy="10" r="8.5" fill="var(--brand-red)"/><path d="M1.5 10 H18.5 M10 1.5 V18.5 M3.5 5.5 H16.5 M3.5 14.5 H16.5" stroke="#fff" stroke-width="1.2"/><ellipse cx="10" cy="10" rx="4" ry="8.5" stroke="#fff" stroke-width="1.2" fill="none"/></svg>
        <span>www.<span class="accent">velmora-buildworks</span>.com</span>
      </p>
    </div>

    <div class="services">
      <p class="services-heading">OUR SERVICES</p>
      <p class="services-list">
        Exhibition Booth Fabrication | Outdoor Booth Setup | Interior Design | Installation and Dismantle<br>
        | Exhibition Management | Shell Scheme Display Booth | Custom Stand Design | Exhibition<br>
        Furniture and Equipment | Exhibition Project Management
      </p>
    </div>
  </section>
</main>
</body>
</html>
```